Redesign existing website

We would like a redesign of the website http://www.vantelquery.com that creates a more modern, up to date look.

Vantel Query creates software for social science research and is focused on making the software user friendly and easy to use. We would like to convey seriousness, but also
a very up to date, just released look.

Feel free to modify the logo if you wish.

Target Market(s)

Academics, researchers

Industry/Entity Type

Software

Requirements
Must have
• The design should incorporate the same information as the current website.

```html
<!DOCTYPE html>
<html lang="en">
<head>
<meta charset="utf-8">
<title>Vantel Query — Empowering the Social Science Researcher</title>
<link href="https://fonts.googleapis.com/css2?family=Poiret+One&family=Arimo:wght@400;700&family=Open+Sans:wght@400;600&display=swap" rel="stylesheet">
<style>
:root{
  --blue-deep:#1c3f9e;
  --blue-mid:#2f58c0;
  --blue-panel:#3a63c6;
  --blue-light:#5aa8ff;
  --blue-pale:#a9c8f5;
  --green:#7ab51d;
  --green-dark:#5c9a0c;
  --text:#5a5a5a;
  --link-blue:#2a5bd7;
  --footer-bg:#dedede;
  --footer-head:#2b4aa8;
  --footer-text:#555;
  --bar:#7a7a7a;
}
*{margin:0;padding:0;box-sizing:border-box}
html,body{width:1200px;height:1000px;overflow:hidden;background:#fff}
body{position:relative;font-family:"Open Sans",sans-serif}
.header-band{position:absolute;left:0;top:0;width:1200px;height:332px;
  background:linear-gradient(180deg,#2447a8 0%,#2a51b6 60%,#2447a6 100%)}
.header-band::after{content:"";position:absolute;left:0;top:270px;width:100%;height:1px;background:#162f78}
.header-panel{position:absolute;left:120px;top:0;width:960px;height:332px;
  background:linear-gradient(180deg,#3b62c4 0%,#3f67c9 80%,#3a62c2 100%);
  box-shadow:0 0 18px rgba(0,0,0,.35)}
.header-panel::after{content:"";position:absolute;left:0;top:270px;width:100%;height:1px;background:#1d3a8a}
.util-nav{position:absolute;left:799px;top:0;width:230px;height:48px;border:1px solid rgba(255,255,255,.18);border-top:none;border-radius:0 0 6px 6px;background:rgba(255,255,255,.05);
  display:flex;align-items:center;justify-content:center;gap:14px;font-size:11px;color:#e8eefc}
.util-nav span{display:flex;align-items:center;gap:6px}
.util-nav .sep{width:1px;height:12px;background:#cfdcf6}
.brand{position:absolute;display:flex;align-items:center;gap:8px;font-family:"Open Sans",sans-serif}
.brand .dot{width:22px;height:22px;border-radius:50%;background:#fff}
.brand-header{left:156px;top:86px;font-size:22px;color:#eaf1ff;font-weight:600}
.tagline{position:absolute;font-family:"Poiret One",sans-serif;color:#fff}
.tag-1{left:155px;top:134px;font-size:28px;color:#fff}
.tag-2{left:222px;top:166px;font-size:50px;color:var(--blue-light)}
.tag-3{left:426px;top:222px;font-size:32px;color:var(--blue-pale)}
.main-nav{position:absolute;left:156px;top:292px;display:flex;font-size:11.5px;color:#fff}
.main-nav a{color:#fff;text-decoration:none;padding:0 17px;border-left:1px solid #fff;line-height:14px}
.main-nav a:first-child{padding-left:0;border-left:none;padding-right:40px}
.hero-photo{position:absolute;left:633px;top:72px;width:399px;height:260px;border:2px solid #fff;
  background:linear-gradient(135deg,#fff 0%,#f3f1ef 45%,#e8c8b0 60%,#f5efe9 80%,#ffffff 100%);
  box-shadow:6px 6px 14px rgba(0,0,0,.35)}
.hero-reflect{position:absolute;left:637px;top:332px;width:392px;height:90px;
  background:linear-gradient(180deg,rgba(210,150,130,.45),rgba(255,255,255,0))}
.content{position:absolute;left:120px;top:332px;width:960px;height:424px;
  background:linear-gradient(180deg,#fafafa 0%,#f1f1f1 70%,#ececec 100%);border:1px solid #d8d8d8;border-top:none}
.welcome-title{position:absolute;left:156px;top:366px;font-family:"Poiret One",sans-serif;font-size:44px;color:var(--green)}
.welcome-text{position:absolute;left:156px;top:433px;width:870px;font-family:"Arimo",sans-serif;font-size:11.6px;line-height:14px;color:var(--text)}
.welcome-text .more{color:var(--green);font-style:italic;font-size:10px;margin-left:14px}
.helps{position:absolute;left:156px;top:525px;font-family:"Arimo",sans-serif;font-size:12.5px;color:#555}
.helps b{font-weight:400;color:var(--green-dark)}
.download{position:absolute;left:744px;top:498px;width:359px;height:63px;border:1px solid #5f9b12;
  background:linear-gradient(180deg,#9dd13a 0%,#84bf22 50%,#74ad14 100%);box-shadow:4px 5px 8px rgba(0,0,0,.3);
  display:flex;align-items:center;padding-left:22px;gap:12px;font-family:"Arimo",sans-serif;color:#fff}
.download .lead{font-family:"Poiret One",sans-serif;font-size:19px;color:#f2ffd8}
.download .name{font-size:20px;color:#2d4a05;margin-left:-6px}
.feature{position:absolute;top:563px;height:140px;background:linear-gradient(180deg,#fff,#f6f6f6);
  box-shadow:0 2px 6px rgba(0,0,0,.22);text-align:center;font-family:"Open Sans",sans-serif;font-size:11.5px;line-height:13.5px;color:var(--link-blue)}
.feature svg,.feature .art{display:block;margin:10px auto 0}
.feature p{position:absolute;left:6px;right:6px;top:90px}
.f1{left:157px;width:180px}.f2{left:354px;width:180px}.f3{left:560px;width:222px}.f4{left:809px;width:222px}
.art-folder{width:76px;height:68px;border-radius:6px;background:linear-gradient(135deg,#f8e7a0,#e6b53a 60%,#7fb0e6)}
.footer{position:absolute;left:120px;top:756px;width:960px;height:204px;background:var(--footer-bg)}
.brand-footer{left:178px;top:860px;font-size:20px;color:var(--blue-deep)}
.brand-footer .dot{background:var(--blue-deep)}
.footer-tag{position:absolute;left:146px;top:903px;width:266px;text-align:center;font-size:10.5px;line-height:13.5px;color:var(--footer-text);letter-spacing:.3px}
.footer-col{position:absolute;top:788px;font-size:10.5px;color:var(--footer-text)}
.footer-col h3{font-size:11px;font-weight:600;color:var(--footer-head);margin-bottom:9px}
.footer-col li{list-style:none;height:24.2px;display:flex;align-items:center;gap:8px}
.footer-col .ic{width:14px;height:14px;background:#5b7bc9;border-radius:2px}
.col-sites{left:542px}.col-products{left:740px}.col-connect{left:925px}
.col-connect li{font-size:11px}
.vline{position:absolute;top:790px;width:1px;height:144px;background:#bdbdbd}
.bottom-bar{position:absolute;left:0;top:960px;width:1200px;height:40px;background:var(--bar);
  font-size:11px;color:#eee;letter-spacing:.2px}
.bottom-bar .copy{position:absolute;left:148px;top:15px}
.bottom-bar .legal{position:absolute;left:912px;top:15px}
.bottom-bar .legal span+span{border-left:1px solid #eee;padding-left:8px;margin-left:10px}
</style>
</head>
<body>
<div class="header-band"></div>
<div class="header-panel"></div>

<nav class="util-nav">
  <span><svg width="14" height="13" viewBox="0 0 14 13"><path d="M1 7 7 1l6 6" fill="#e07a20"/><rect x="3" y="6" width="8" height="6" fill="#f0c070"/></svg>Home</span>
  <span class="sep"></span>
  <span><svg width="11" height="13" viewBox="0 0 11 13"><path d="M2.5 6V4a3 3 0 0 1 6 0v2" stroke="#ddd" stroke-width="1.6" fill="none"/><rect x="1" y="6" width="9" height="7" rx="1" fill="#eee"/></svg>Login</span>
</nav>

<div class="brand brand-header"><span class="dot"></span>Vantel Query</div>
<div class="tagline tag-1">Empowering The</div>
<div class="tagline tag-2">Social Science</div>
<div class="tagline tag-3">RESEARCHER</div>

<nav class="main-nav"><a>Home</a><a>Products</a><a>News</a><a>About Us</a><a>Contact Us</a></nav>

<div class="content"></div>
<div class="hero-reflect"></div>
<div class="hero-photo" role="img" aria-label="Photo of a hand holding a pen touching a water surface with ripples"></div>

<h1 class="welcome-title">WELCOME</h1>
<p class="welcome-text">The mission of Vantel Query, Inc. is to produce software products that multiply the power and efficiency of empirical scientific research in the social sciences. A central goal is to expand access to complex data sources and to the advanced methods of scientific investigation needed to analyze them. Reliance on antiquated data management tools imposes heavy costs on the research community. The VDM reduces the costs of research by allowing analysts to manipulate data without the assistance of professional programming staff. <span class="more">read more...</span></p>

<p class="helps">THE <b>VANTEL DATA MANAGER (VDM)</b> HELPS RESEARCHERS:</p>

<a class="download">
  <svg width="18" height="26" viewBox="0 0 18 26"><rect x="5" y="0" width="8" height="14" fill="#f2b21c"/><path d="M0 13h18L9 26z" fill="#e79a10"/></svg>
  <span class="lead">DOWNLOAD</span><span class="name">Vantel Data Manager</span>
</a>

<div class="feature f1">
  <div class="art art-folder" role="img" aria-label="Illustration of a folder linked to networked computers"></div>
  <p>Integrate data from different periods, places, and sources</p>
</div>
<div class="feature f2">
  <svg width="64" height="66" viewBox="0 0 64 66"><rect x="1" y="2" width="22" height="62" fill="#8fcc1a"/><rect x="28" y="16" width="18" height="48" fill="#7fa8e8"/><rect x="50" y="36" width="12" height="28" fill="#f08a10"/></svg>
  <p>Restructure complex data structures for analysis</p>
</div>
<div class="feature f3">
  <svg width="66" height="62" viewBox="0 0 66 62"><ellipse cx="33" cy="36" rx="31" ry="24" fill="#2a4f7a"/><ellipse cx="33" cy="30" rx="31" ry="27" fill="#6d9fd0"/><path d="M33 30 64 28a31 27 0 0 1-12 22z" fill="#4ebd3a"/></svg>
  <p>Generate simple descriptive statistics for diagnostic purposes and feasibility analyses</p>
</div>
<div class="feature f4">
  <svg width="50" height="50" viewBox="0 0 50 50"><rect x="2" y="4" width="46" height="30" fill="#fff" stroke="#999"/><rect x="10" y="24" width="5" height="6" fill="#6a1fb0"/><rect x="19" y="18" width="5" height="12" fill="#6a1fb0"/><rect x="28" y="14" width="5" height="16" fill="#6a1fb0"/><path d="M25 34v10M25 38l-10 10M25 38l10 10" stroke="#777" stroke-width="2"/></svg>
  <p>Export subsets of variables and cases in formats suitable for analysis in any statistical package.</p>
</div>

<footer>
  <div class="footer"></div>
  <div class="brand brand-footer"><span class="dot"></span>Vantel Query</div>
  <p class="footer-tag">Increasing The Power And Efficiency Of Empirical Social Science Research</p>
  <span class="vline" style="left:469px"></span>
  <span class="vline" style="left:666px"></span>
  <span class="vline" style="left:864px"></span>
  <div class="footer-col col-sites"><h3>SITE LINKS</h3><ul><li>Home</li><li>Products</li><li>News</li><li>About Us</li><li>Contact Us</li></ul></div>
  <div class="footer-col col-products"><h3>PRODUCTS</h3><ul><li>Overview</li><li>Features</li><li>Datasets</li><li>Screenshots</li><li>Support</li></ul></div>
  <div class="footer-col col-connect"><h3>CONNECT WITH US</h3><ul>
    <li><span class="ic"></span>Chirpline</li>
    <li><span class="ic"></span>Friendwall</li>
    <li><span class="ic"></span>Clipstream</li>
    <li><span class="ic" style="background:#f08a20"></span>Rss Feed</li>
    <li><svg width="14" height="10" viewBox="0 0 14 10"><rect x=".5" y=".5" width="13" height="9" fill="#eef3fb" stroke="#6d8cc8"/><path d="M.5.5 7 6l6.5-5.5" fill="none" stroke="#6d8cc8"/></svg>Email</li>
  </ul></div>
  <div class="bottom-bar">
    <span class="copy">Copyright © Vantel Query 2011. All Rights Reserved.</span>
    <span class="legal"><span>Privacy Policy</span><span>Disclaimer</span></span>
  </div>
</footer>
</body>
</html>
```